Letterhead and matching envelope design for a dental office

We need a new stationary design, letterhead and envelope #10, for a dental office in Denver area. We are called Bright Harbor Dental. We want a simple and minimalistic design but not a boring design. I wish to have one good point that makes it look professional. I have attached our logo. Feel free to use either one. I want the design for letterhead and envelope look like a "matching pair" but not look the same. The envelope doesn't have to be white and it will have an address window on bottom left.

Target Market(s)

everyone who visits dentist (adults)

Industry/Entity Type

Dental

Font styles to use
Other font styles liked:
• close to font on logo or something that matches well

Requirements
Must have
• professional
• simple, minimalistic
• unique point that stands out
Nice to have
• matching but not same design for letterhead and envelope
Should not have
• not look like all the other boring designs
• no flowery, distracting feats

```html
<!DOCTYPE html>
<html lang="en">
<head>
<meta charset="utf-8">
<title>Bright Harbor Dental – Letterhead</title>
<link href="https://fonts.googleapis.com/css2?family=Lato:wght@400;700&display=swap" rel="stylesheet">
<style>
  :root {
    --backdrop: #e9e9ea;
    --paper: #ffffff;
    --brand-green: #3bb54a;
    --brand-green-soft: #bfe3c2;
    --ink: #2b2b2b;
    --ink-muted: #555555;
    --signature-blue: #2a3a8f;
  }
  * { box-sizing: border-box; margin: 0; padding: 0; }
  html, body {
    width: 1200px; height: 795px; overflow: hidden;
    background: var(--backdrop);
    font-family: "Lato", "Helvetica Neue", Arial, sans-serif;
    color: var(--ink);
  }
  .letterhead {
    position: absolute; left: 338px; top: 24px;
    width: 524px; height: 747px;
    background: var(--paper);
    box-shadow: 0 2px 10px rgba(0,0,0,0.12);
    overflow: hidden;
  }
  .brand {
    position: absolute; left: 40px; top: 40px;
    display: flex; align-items: center; gap: 7px;
  }
  .brand-dot {
    width: 12px; height: 12px; border-radius: 50%;
    background: var(--brand-green);
  }
  .brand-name {
    font-size: 13px; font-weight: 700; letter-spacing: 2px;
    text-transform: uppercase; color: var(--brand-green);
  }
  .contact {
    position: absolute; right: 40px; top: 36px;
    text-align: right; font-size: 8.5px; line-height: 1.45;
    font-style: normal; color: var(--ink);
  }
  .contact-company { color: var(--brand-green); }
  .contact-line { display: flex; justify-content: flex-end; align-items: center; gap: 4px; }
  .contact-icon { width: 9px; height: 9px; flex: none; }
  .letter-body {
    position: absolute; left: 60px; top: 150px; width: 400px;
    font-size: 8.4px; line-height: 1.38; color: var(--ink-muted);
  }
  .salutation { font-weight: 700; font-size: 9px; color: var(--ink); margin-bottom: 12px; }
  .letter-body p { margin-bottom: 13px; }
  .closing { margin-top: 24px; font-size: 9px; color: var(--ink); line-height: 1.35; }
  .signature {
    width: 100px; height: 22px; margin: 4px 0 6px;
    background: linear-gradient(90deg, rgba(42,58,143,0.25), rgba(42,58,143,0.08));
    border-radius: 2px;
  }
  .footer-website {
    position: absolute; right: 40px; bottom: 40px;
    font-size: 9px; letter-spacing: 0.6px; color: var(--brand-green);
  }
  .footer-rule-thin {
    position: absolute; left: 0; right: 0; bottom: 30px; height: 4px;
    background: var(--brand-green-soft);
  }
  .footer-band {
    position: absolute; left: 0; right: 0; bottom: 0; height: 24px;
    background: var(--brand-green);
  }
</style>
</head>
<body>
  <main class="letterhead">
    <div class="brand">
      <span class="brand-dot"></span>
      <span class="brand-name">Bright Harbor Dental</span>
    </div>

    <address class="contact">
      <div class="contact-company">Bright Harbor Dental</div>
      <div>2870 Lakeview Ave</div>
      <div>Suite 210 Arvada, CO 80002</div>
      <div class="contact-line">720-555-0148
        <svg class="contact-icon" viewBox="0 0 10 10" aria-hidden="true">
          <circle cx="5" cy="5" r="5" fill="#3bb54a"/>
          <path d="M3.3 2.6c.3 0 .5.6.6 1 .1.3-.4.5-.3.8.2.5.6.9 1.1 1.1.3.1.5-.4.8-.3.4.1 1 .3 1 .6 0 .5-.6.9-1 .9C3.9 6.6 2.4 5.1 2.3 3.5c0-.4.5-.9 1-.9z" fill="#fff"/>
        </svg>
      </div>
      <div class="contact-line">info@brightharbordental.com
        <svg class="contact-icon" viewBox="0 0 10 10" aria-hidden="true">
          <circle cx="5" cy="5" r="5" fill="#3bb54a"/>
          <rect x="2.4" y="3.2" width="5.2" height="3.6" rx="0.4" fill="#fff"/>
          <path d="M2.6 3.4L5 5.3l2.4-1.9" stroke="#3bb54a" stroke-width="0.6" fill="none"/>
        </svg>
      </div>
    </address>

    <section class="letter-body">
      <div class="salutation">Dear Mr. Carter,</div>
      <p>Lorem Ipsum is simply dummy text of the printing and typesetting industry. Lorem Ipsum has been the industry's standard dummy text ever since the 1500s, when an unknown printer took a galley of type and scrambled it to make a type specimen book. It has survived not only five centuries, but also the leap into electronic typesetting, remaining essentially unchanged.</p>
      <p>The standard chunk of Lorem Ipsum used since the 1500s is reproduced below for those interested. Sections 1.10.32 and 1.10.33 from "de Rebus Lucis et Umbrae" by Quintus Arvel are also reproduced in their exact original form, accompanied by English versions from the 1914 translation by H. Pellworth.</p>
      <p>Lorem Ipsum is simply dummy text of the printing and typesetting industry. Lorem Ipsum has been the industry's standard dummy text ever since the 1500s, when an unknown printer took a galley of type and scrambled it to make a type specimen book. It has survived not only five centuries, but also the leap into electronic typesetting, remaining essentially unchanged. It was popularised in the</p>
      <div class="closing">
        <div>Sincerely Your,</div>
        <div class="signature" role="img" aria-label="Handwritten signature in blue ink"></div>
        <div>Name Last Name</div>
        <div>Company Name</div>
      </div>
    </section>

    <div class="footer-website">www.brightharbordental.com</div>
    <div class="footer-rule-thin"></div>
    <div class="footer-band"></div>
  </main>
</body>
</html>
```